Upgrade 4 Images - Bid 1, then we can discuss the other 3

We have a four graphics that we use in various presentations and business proposals. We want to upgrade them to make them really pop and match the level of service we provide, without going overboard.

We're open to new ideas, but the general form and content should stay the same.

I'd like to have all four designed by the same person, but I'm assuming this bid will be for 1 of the four, and then the other three can be contracted as additions.

```html
<!DOCTYPE html>
<html lang="en">
<head>
<meta charset="utf-8">
<title>Operating Quadrants – Data Processing as a Service</title>
<link rel="stylesheet" href="https://fonts.googleapis.com/css2?family=Open+Sans:wght@400;600&display=swap">
<style>
  :root {
    --teal: #033b3d;
    --orange: #ed7f33;
    --grey: #6d6e71;
    --paper: #ffffff;
  }
  html, body {
    margin: 0;
    padding: 0;
    overflow: hidden;
    background: var(--paper);
  }
  .canvas {
    position: relative;
    width: 1200px;
    height: 893px;
    overflow: hidden;
    background: var(--paper);
    font-family: "Open Sans", "Segoe UI", sans-serif;
  }
  .title {
    position: absolute;
    left: 0;
    width: 1158px;
    top: 24px;
    margin: 0;
    text-align: center;
    font-weight: 400;
    font-size: 64px;
    line-height: 1;
    color: var(--teal);
    letter-spacing: 0.5px;
  }
  .subtitle {
    position: absolute;
    left: 0;
    width: 1158px;
    top: 97px;
    margin: 0;
    text-align: center;
    font-weight: 400;
    font-size: 21px;
    color: var(--teal);
  }
  .matrix {
    position: absolute;
    left: 0;
    top: 0;
    width: 1200px;
    height: 893px;
  }
  .axis-label {
    font-family: "Open Sans", "Segoe UI", sans-serif;
    font-size: 21px;
    fill: var(--grey);
  }
  .quadrant-label {
    font-family: "Open Sans", "Segoe UI", sans-serif;
    font-size: 22px;
    fill: var(--paper);
  }
  .zone-label {
    font-family: "Open Sans", "Segoe UI", sans-serif;
    font-size: 21px;
    fill: var(--grey);
  }
  .brand {
    position: absolute;
    left: 770px;
    top: 688px;
    display: flex;
    align-items: center;
    gap: 12px;
    white-space: nowrap;
  }
  .brand-mark {
    width: 18px;
    height: 18px;
    background: var(--orange);
  }
  .brand-name {
    margin: 0;
    font-size: 40px;
    font-weight: 600;
    line-height: 1;
    color: var(--orange);
  }
  .web {
    position: absolute;
    left: 0;
    width: 1158px;
    top: 821px;
    margin: 0;
    text-align: center;
    font-size: 18px;
    color: var(--teal);
  }
</style>
</head>
<body>
<div class="canvas">
  <h1 class="title">Operating Quadrants</h1>
  <p class="subtitle">Data Processing as a Service</p>

  <svg class="matrix" viewBox="0 0 1200 893" aria-label="Operating quadrants matrix: maturity against utilization">
    <defs>
      <clipPath id="square-clip">
        <rect x="439" y="328" width="276" height="276" rx="24"/>
      </clipPath>
      <filter id="lift" x="-20%" y="-20%" width="140%" height="140%">
        <feDropShadow dx="3" dy="4" stdDeviation="4" flood-color="#000" flood-opacity="0.25"/>
      </filter>
      <radialGradient id="zone-glow" cx="50%" cy="50%" r="50%">
        <stop offset="0.6" stop-color="#ffffff"/>
        <stop offset="1" stop-color="#e4e4e4"/>
      </radialGradient>
    </defs>

    <g class="axes" stroke="var(--grey)" stroke-width="1" stroke-dasharray="3 3" fill="none">
      <line x1="577" y1="231" x2="577" y2="328"/>
      <line x1="577" y1="604" x2="577" y2="697"/>
      <line x1="349" y1="466" x2="439" y2="466"/>
      <line x1="715" y1="465" x2="809" y2="465"/>
    </g>
    <circle cx="577" cy="231" r="4" fill="var(--orange)"/>
    <circle cx="577" cy="697" r="4" fill="var(--orange)"/>
    <circle cx="349" cy="466" r="4" fill="var(--teal)"/>
    <circle cx="809" cy="465" r="4" fill="var(--teal)"/>

    <text class="axis-label" x="578" y="217" text-anchor="middle">High Maturity</text>
    <text class="axis-label" x="578" y="727" text-anchor="middle">Low Maturity</text>
    <text class="axis-label" x="332" y="473" text-anchor="end">Low Utilization</text>
    <text class="axis-label" x="820" y="473">High Utilization</text>

    <g filter="url(#lift)">
      <g clip-path="url(#square-clip)">
        <rect x="439" y="328" width="276" height="276" fill="url(#zone-glow)"/>
        <path class="quadrant specialist" d="M439 328 H577 A138 138 0 0 1 439 466 Z" fill="var(--teal)"/>
        <path class="quadrant enterprise" d="M715 328 V466 A138 138 0 0 1 577 328 Z" fill="var(--orange)"/>
        <path class="quadrant ad-hoc" d="M439 604 V466 A138 138 0 0 1 577 604 Z" fill="var(--orange)"/>
        <path class="quadrant factory" d="M715 604 H577 A138 138 0 0 1 715 466 Z" fill="var(--teal)"/>
      </g>
    </g>

    <text class="quadrant-label" transform="translate(511 398) rotate(-45)" text-anchor="middle">Specialist</text>
    <text class="quadrant-label" transform="translate(645 404) rotate(45)" text-anchor="middle">Enterprise</text>
    <text class="quadrant-label" transform="translate(500 550) rotate(45)" text-anchor="middle">Ad Hoc</text>
    <text class="quadrant-label" transform="translate(656 546) rotate(-45)" text-anchor="middle">Factory</text>

    <text class="zone-label" x="581" y="464" text-anchor="middle">Goldilocks</text>
    <text class="zone-label" x="581" y="490" text-anchor="middle">Zone</text>
  </svg>

  <div class="brand">
    <span class="brand-mark"></span>
    <p class="brand-name">Corvane Group</p>
  </div>

  <p class="web">www.corvanegroup.com</p>
</div>
</body>
</html>
```